BRIGHT RIVER POWER.

I'd like my business logo.
contact name: Dennis Halvorsen
phone:0438759164
email: info@brightriverpower.net.au
website: www.brightriverpower.net.au

services:
solar
battery storage
LED lighting
energy saving solutions
general electrical
I'd like the design to look professional

Target Market(s)

Everyone

Industry/Entity Type

Business

Contact Information for Business Card

as described above

Requirements
Must have
• Id like the colours and the design to work well with my logo.

```html
<!DOCTYPE html>
<html lang="en">
<head>
<meta charset="utf-8">
<title>Bright River Power – Business Card</title>
<link rel="stylesheet" href="https://fonts.googleapis.com/css2?family=Open+Sans:wght@400;600;700&display=swap">
<style>
  :root {
    --bg: #ecebe7;
    --green-light: #8cc63f;
    --green-mid: #6cbf5a;
    --green-deep: #4fb36f;
    --orange: #f7a21b;
    --orange-deep: #f08a12;
    --white: #ffffff;
    --paper: #f4f4f4;
    --text-white: #ffffff;
  }
  * { margin: 0; padding: 0; box-sizing: border-box; }
  html, body {
    width: 1200px; height: 900px; overflow: hidden;
    background: var(--bg);
    font-family: "Open Sans", Arial, sans-serif;
  }
  .stage {
    width: 1200px; height: 900px;
    display: flex; align-items: center; justify-content: center; gap: 40px;
  }
  .card {
    width: 540px; height: 310px; position: relative; overflow: hidden;
    box-shadow: 0 6px 18px rgba(0,0,0,0.18);
  }

  /* Front */
  .card-front {
    background: linear-gradient(160deg, var(--green-deep) 0%, var(--green-mid) 45%, var(--green-light) 100%);
    display: flex; align-items: center; justify-content: center;
  }
  .brand {
    display: flex; align-items: center; gap: 14px;
    font-weight: 700; letter-spacing: 1px; white-space: nowrap;
  }
  .brand-dot { width: 34px; height: 34px; border-radius: 50%; flex: none; }
  .card-front .brand { color: var(--text-white); font-size: 34px; }
  .card-front .brand-dot { background: var(--white); }

  /* Back */
  .card-back { background: var(--white); }
  .back-top {
    position: absolute; left: 0; top: 0; width: 100%; height: 160px;
    background: linear-gradient(180deg, var(--white) 0%, var(--paper) 100%);
    display: flex; align-items: center; justify-content: center;
  }
  .card-back .brand { color: var(--green-deep); font-size: 30px; }
  .card-back .brand-dot { background: var(--orange); width: 30px; height: 30px; }
  .back-stripe {
    position: absolute; left: 0; top: 160px; width: 100%; height: 6px;
    background: linear-gradient(90deg, var(--orange-deep), var(--orange));
  }
  .back-bottom {
    position: absolute; left: 0; top: 166px; width: 100%; height: 144px;
    background: linear-gradient(90deg, var(--green-light) 0%, var(--green-mid) 60%, var(--green-deep) 100%);
    color: var(--text-white);
  }
  .contact { position: absolute; left: 34px; top: 26px; }
  .contact-name { font-size: 21px; font-weight: 600; margin-bottom: 8px; line-height: 28px; }
  .contact-line {
    display: flex; align-items: center; gap: 10px;
    font-size: 14px; line-height: 21px;
  }
  .contact-line svg { width: 12px; height: 12px; flex: none; }
  .services { position: absolute; right: 26px; top: 10px; text-align: right; }
  .services-title { font-size: 14px; letter-spacing: 0.5px; line-height: 20px; margin-bottom: 2px; }
  .services-list { list-style: none; }
  .services-list li {
    font-size: 12px; line-height: 18px;
    display: flex; justify-content: flex-end; align-items: center; gap: 7px;
  }
  .services-list li::after {
    content: ""; width: 6px; height: 6px; border-radius: 50%; background: var(--white);
  }
</style>
</head>
<body>
<main class="stage">
  <section class="card card-front" aria-label="Business card front">
    <div class="brand"><span class="brand-dot"></span>BRIGHT RIVER POWER</div>
  </section>

  <section class="card card-back" aria-label="Business card back">
    <div class="back-top">
      <div class="brand"><span class="brand-dot"></span>BRIGHT RIVER POWER</div>
    </div>
    <div class="back-stripe"></div>
    <div class="back-bottom">
      <div class="contact">
        <p class="contact-name">Dennis Halvorsen</p>
        <p class="contact-line">
          <svg viewBox="0 0 12 12" aria-hidden="true"><path fill="#fff" d="M2 1h2.5l1 2.5-1.3 1a6 6 0 0 0 3.3 3.3l1-1.3 2.5 1V10a1 1 0 0 1-1 1A9.5 9.5 0 0 1 1 2a1 1 0 0 1 1-1z"/></svg>
          0438759164
        </p>
        <p class="contact-line">
          <svg viewBox="0 0 12 12" aria-hidden="true"><rect x="0.5" y="2" width="11" height="8" fill="#fff"/><path d="M0.5 2.5 6 6.5l5.5-4" stroke="#6cbf5a" fill="none"/></svg>
          info@brightriverpower.net.au
        </p>
        <p class="contact-line">
          <svg viewBox="0 0 12 12" aria-hidden="true"><path d="M5 7l2-2M4.5 5.5 3 7a1.8 1.8 0 0 0 2.5 2.5L7 8M7.5 6.5 9 5a1.8 1.8 0 0 0-2.5-2.5L5 4" stroke="#fff" stroke-width="1.3" fill="none" stroke-linecap="round"/></svg>
          www.brightriverpower.net.au
        </p>
      </div>
      <div class="services">
        <p class="services-title">WHAT I DO</p>
        <ul class="services-list">
          <li>Solar</li>
          <li>Battery Storage</li>
          <li>LED Lighting</li>
          <li>Energy Saving Solutions</li>
          <li>General Electrical</li>
        </ul>
      </div>
    </div>
  </section>
</main>
</body>
</html>
```